Sustainably Transforming Education

Company is education services based. early learning through adult and corporate. Focus is national government policy and program design and delivery alongside a research based and academically grounded set of approaches to planning, evaluation, and change management.I am looking for an innovative design position that aligns with the global agendas for innovation, creativity and collaboration at international and national policy levels (berulo is a name that reflects these qualities - colours need to reflect amythyst in some way). I also need a design that translates from a business card as 1 medium of interaction to a template that can work in word/powerpoint etc to support both stationery as well as a digital strategy across multiple channels (fb/twit/etc)There is no slogan/tag line for the company and their is no logo. I was looking to just leverage the name - have currently played around with various fonts (ending up with cuisine - all lowercase).

Industry/Entity Type

Adult

Contact Information for Business Card

name: berulo (all lowercase)Chairman: Andrew CrowMobile: +61 418 902 131Web: www.berulo.comemail: martin.pelly@berulo-example.com

Font styles to use
Script
Other font styles liked:
• cuisine

Colors
e34298
e667a6
33a6d7
aaaaaa

Requirements
Nice to have
• https://files.example-share.net/sh/qx7kw2hd91lzmnp/AAFr3tYbQeLp8VwZnKcDs2Hu?dl=0
• Link to the printwell templates used to begin this process....the one with the lines was about people intersecting (collaborating).....the organic shapes one more of a fluid feel of people coming together - the overall shape being largely spherical could represent a "global" feel.....anyway that is how I was thinking about these

```html
<!DOCTYPE html>
<html lang="en">
<head>
<meta charset="utf-8">
<title>berulo</title>
<link href="https://fonts.googleapis.com/css2?family=Damion&display=swap" rel="stylesheet">
<style>
  :root {
    --amethyst-pink: #e34298;
    --soft-pink: #e667a6;
    --sky-blue: #33a6d7;
    --map-blue: #6db5e0;
    --white: #ffffff;
  }
  html, body {
    margin: 0;
    padding: 0;
    width: 1200px;
    height: 740px;
    overflow: hidden;
    background: var(--sky-blue);
  }
  .card {
    position: relative;
    width: 1200px;
    height: 740px;
    background: var(--sky-blue);
    overflow: hidden;
  }
  .card__waves {
    position: absolute;
    inset: 0;
    width: 1200px;
    height: 740px;
  }
  .wave--deep { fill: var(--amethyst-pink); }
  .wave--soft { fill: var(--soft-pink); }
  .card__map {
    position: absolute;
    left: 272px;
    top: 132px;
    width: 742px;
    height: 480px;
    border-radius: 42% 46% 38% 44% / 40% 44% 48% 42%;
    background: radial-gradient(ellipse at 50% 45%, var(--map-blue) 0%, rgba(109,181,224,0.55) 60%, rgba(109,181,224,0) 100%);
  }
  .card__name {
    position: absolute;
    left: 0;
    right: 0;
    top: 292px;
    margin: 0;
    text-align: center;
    font-family: "Damion", cursive;
    font-weight: 400;
    font-size: 118px;
    line-height: 1;
    letter-spacing: 2px;
    color: var(--white);
    transform: translateX(-6px);
  }
</style>
</head>
<body>
  <main class="card">
    <svg class="card__waves" viewBox="0 0 1200 740" aria-hidden="true">
      <path class="wave--soft" d="M468 0 C700 30 900 40 1020 110 C1120 170 1180 330 1200 520 L1200 0 Z"/>
      <path class="wave--deep" d="M780 0 C900 30 1000 70 1040 130 C1120 200 1170 330 1200 440 L1200 0 Z"/>
      <path class="wave--deep" d="M0 156 C80 330 200 560 492 740 L0 740 Z"/>
      <path class="wave--soft" d="M0 156 C60 300 150 470 300 600 C200 500 100 360 0 210 Z"/>
    </svg>
    <div class="card__map" role="img" aria-label="Faint light-blue world map spread across the centre of the card"></div>
    <h1 class="card__name">berulo</h1>
  </main>
</body>
</html>
```